Business Card Design

I need business cards designed for a new company i have started that makes cakes, particularly themed kids cakes with a really modern design and I would like to have my business cards reflect this. I have attached some photos of cakes I have made and would like some to be used.

Industry/Entity Type

Business

Contact Information for Business Card

Business Name: Tarts and Treats by Maren
Mobile: 0492 815 063
email: maren@tartsandtreatsbymaren.example.au
Instagram: instagram.com/tartsandtreatsbymaren/
Facebook: fb.me/tartsandtreatsbymaren

Colors
e667a6
b768aa
3276b5

Requirements
Must have
• Business Name: Tarts and Treats by Maren
• Mobile: 0492 815 063
• email: maren@tartsandtreatsbymaren.example.au
• Instagram: instagram.com/tartsandtreatsbymaren/
• Facebook: fb.me/tartsandtreatsbymaren
Nice to have
• 2 to 3 pictures of my cakes

```html
<!DOCTYPE html>
<html lang="en">
<head>
<meta charset="utf-8">
<title>Tarts and Treats by Maren — Business Cards</title>
<link rel="stylesheet" href="https://fonts.googleapis.com/css2?family=Source+Sans+3:wght@400;600&display=swap">
<style>
  :root {
    --pink: #e667a6;
    --pink-soft: #f4b9d6;
    --pink-pale: #fbe3ef;
    --plum: #b768aa;
    --card: #ffffff;
    --card-edge: #ececec;
    --stage: #e4e6e8;
    --grey-flourish: #efefef;
  }
  * { margin: 0; padding: 0; box-sizing: border-box; }
  html, body { width: 1200px; height: 1200px; overflow: hidden; }
  body {
    background: var(--stage);
    font-family: "Source Sans 3", "Myriad Pro", Arial, sans-serif;
    position: relative;
  }
  .card {
    position: absolute;
    left: 200px;
    width: 790px;
    height: 463px;
    background: radial-gradient(ellipse at 55% 45%, var(--card) 55%, var(--card-edge) 100%);
    overflow: hidden;
  }
  .card--front { top: 67px; }
  .card--back { top: 622px; }

  .flourish { position: absolute; display: block; }
  .flourish--front-main { left: 110px; top: 0; width: 620px; height: 463px; }
  .flourish--front-faint { left: 0; top: 0; width: 330px; height: 463px; }
  .flourish--back-top { left: 0; top: 0; width: 790px; height: 270px; }

  .brand {
    position: absolute;
    color: var(--plum);
    font-weight: 400;
    text-align: center;
    line-height: 1.05;
  }
  .brand--front { left: 48px; top: 70px; width: 160px; font-size: 30px; }
  .brand--back { left: 60px; top: 270px; width: 120px; font-size: 22px; }
  .brand__line { display: block; }
  .brand__mark {
    display: block;
    margin: 0 auto 10px;
    width: 12px; height: 12px;
    border-radius: 50%;
    background: var(--pink);
  }

  .mobile {
    position: absolute;
    left: 549px; top: 398px;
    padding: 4px 8px;
    border: 2px solid var(--pink-soft);
    background: var(--card);
    color: var(--plum);
    font-size: 18px;
    line-height: 1.2;
    white-space: nowrap;
  }

  .contacts {
    position: absolute;
    left: 410px; top: 348px;
    list-style: none;
    color: var(--plum);
    font-size: 16.5px;
    line-height: 21px;
  }
  .contacts__item { display: flex; align-items: center; gap: 7px; white-space: nowrap; }
  .contacts__icon { width: 13px; height: 13px; flex: none; }
  .contacts__square { width: 11px; height: 11px; background: var(--plum); border-radius: 2px; flex: none; margin: 0 1px; }
</style>
</head>
<body>

<section class="card card--front" aria-label="Business card front">
  <svg class="flourish flourish--front-faint" viewBox="0 0 330 463" role="img" aria-label="Faint grey floral swirl pattern">
    <defs>
      <radialGradient id="faint-grey" cx="40%" cy="45%" r="65%">
        <stop offset="0" stop-color="var(--grey-flourish)" stop-opacity="0.9"/>
        <stop offset="1" stop-color="var(--grey-flourish)" stop-opacity="0"/>
      </radialGradient>
    </defs>
    <rect width="330" height="463" fill="url(#faint-grey)"/>
  </svg>

  <svg class="flourish flourish--front-main" viewBox="0 0 620 463" role="img" aria-label="Pink floral swirl ornament with flowers and leaves sweeping from the top right down to the bottom">
    <defs>
      <linearGradient id="front-swirl" x1="0" y1="1" x2="1" y2="0">
        <stop offset="0" stop-color="var(--pink-pale)"/>
        <stop offset="0.5" stop-color="var(--pink-soft)"/>
        <stop offset="1" stop-color="var(--pink)"/>
      </linearGradient>
    </defs>
    <path d="M600 0 C470 20 400 110 410 200 C420 290 330 330 240 380 C170 420 120 450 90 463 L420 463 C400 420 460 360 470 300 C490 200 540 120 620 60 L620 0 Z" fill="url(#front-swirl)" opacity="0.75"/>
  </svg>

  <div class="brand brand--front">
    <span class="brand__mark"></span>
    <span class="brand__line">Tarts</span>
    <span class="brand__line">and Treats</span>
    <span class="brand__line">by Maren</span>
  </div>

  <p class="mobile">Mobile: 0492 815 063</p>
</section>

<section class="card card--back" aria-label="Business card back">
  <svg class="flourish flourish--back-top" viewBox="0 0 790 270" role="img" aria-label="Pink floral swirl ornament with flowers and leaves across the top edge">
    <defs>
      <linearGradient id="back-swirl" x1="0" y1="0" x2="0" y2="1">
        <stop offset="0" stop-color="var(--pink)"/>
        <stop offset="0.55" stop-color="var(--pink-soft)"/>
        <stop offset="1" stop-color="var(--pink-pale)" stop-opacity="0"/>
      </linearGradient>
    </defs>
    <path d="M0 0 L790 0 L790 140 C700 150 620 200 540 190 C450 180 400 200 330 240 C290 260 260 230 240 200 C200 150 120 130 0 130 Z" fill="url(#back-swirl)" opacity="0.8"/>
  </svg>

  <div class="brand brand--back">
    <span class="brand__mark"></span>
    <span class="brand__line">Tarts</span>
    <span class="brand__line">and Treats</span>
    <span class="brand__line">by Maren</span>
  </div>

  <ul class="contacts">
    <li class="contacts__item">
      <svg class="contacts__icon" viewBox="0 0 13 13" aria-hidden="true">
        <rect x="0.5" y="2.5" width="12" height="8.5" rx="1" fill="var(--plum)"/>
        <path d="M1 3 L6.5 7.5 L12 3" fill="none" stroke="#fff" stroke-width="1.2"/>
      </svg>
      maren@tartsandtreatsbymaren.example.au
    </li>
    <li class="contacts__item"><span class="contacts__square"></span>instagram.com/tartsandtreatsbymaren/</li>
    <li class="contacts__item"><span class="contacts__square"></span>fb.me/tartsandtreatsbymaren</li>
  </ul>
</section>

</body>
</html>
```